BUSINESS CARD - HALLORAN FIELD SERVICES

I would like to create a business card for my fertilizer spreading business. I would like to incorporate my existing logo and also a description of the services offered. The business card will be given to farmers so must be kept simple but effective. It will also be left in stores so much also be eye catching in order to stand out from other cards.

Target Market(s)

FARMERS

Requirements
Must have
• FRONT OF CARD = EXISTING LOGO + "CUSTOMISED SPREADING" below the logo

REAR Of CARD = SERVICES OFFERED AND CONTACT DETAILS

- Bulk fertilizer including Lime, Gypsum, Manure & Compost
- Granular fertilizer including Single Super, Urea, Gran-am, & Custom Blends
- Modern equipment - Autosteer & Variable Rate Capable
- Friendly & Reliable Service
- Contact Gus: 0417 552 308
Nice to have
• utilize same color scheme as existing logo

```html
<!DOCTYPE html>
<html lang="en">
<head>
<meta charset="utf-8">
<title>Halloran Field Services – Business Card</title>
<link href="https://fonts.googleapis.com/css2?family=Roboto:wght@400;700&family=Exo+2:wght@700&display=swap" rel="stylesheet">
<style>
  :root {
    --backdrop: #d6d6d6;
    --paper: #ffffff;
    --charcoal: #58585a;
    --charcoal-dark: #4a4a4c;
    --orange: #f7941d;
    --white: #ffffff;
    --silver: #c4c4c6;
    --slate-text: #8e8e90;
  }
  * { margin: 0; padding: 0; box-sizing: border-box; }
  html, body {
    width: 1200px; height: 801px; overflow: hidden;
    background: var(--backdrop);
    font-family: "Roboto", Arial, sans-serif;
  }
  .card {
    position: absolute; top: 274px;
    width: 443px; height: 263px; overflow: hidden;
  }
  .card--services { left: 153px; background: var(--paper); }
  .card--brand { left: 625px; background: var(--charcoal); }

  .wave { position: absolute; inset: 0; width: 443px; height: 263px; }

  .brand-mark {
    position: absolute; left: 307px; top: 22px;
    width: 66px; height: 66px; border-radius: 50%;
    background: var(--charcoal);
  }
  .brand-name {
    position: absolute; right: 26px; top: 90px;
    font-weight: 700; font-size: 13.5px; color: var(--charcoal);
    white-space: nowrap;
  }

  .service-list { position: absolute; left: 31px; top: 113px; list-style: none; }
  .service-list li {
    position: relative; padding-left: 12px; margin-bottom: 4.5px;
    color: var(--white); font-size: 12.6px; line-height: 14.8px;
  }
  .service-list li::before {
    content: ""; position: absolute; left: 0; top: 4px;
    width: 8px; height: 8px; border-radius: 50%; background: var(--orange);
  }

  .contact { position: absolute; left: 310px; top: 208px; }
  .contact-name { color: var(--orange); font-size: 18px; line-height: 22px; }
  .contact-phone { color: var(--white); font-size: 18px; line-height: 22px; }

  .brand-mark--large {
    position: absolute; left: 165px; top: 50px;
    width: 110px; height: 110px; border-radius: 50%;
    background: var(--charcoal-dark);
  }
  .brand-name--large {
    position: absolute; left: 0; right: 0; top: 160px; text-align: center;
    font-weight: 700; font-size: 22px; color: var(--silver);
  }
  .tagline {
    position: absolute; left: 0; right: 0; top: 215px; text-align: center;
    font-family: "Exo 2", Arial, sans-serif; font-weight: 700;
    font-size: 18.5px; letter-spacing: 0.3px; color: var(--slate-text);
  }
</style>
</head>
<body>
  <section class="card card--services">
    <svg class="wave" viewBox="0 0 443 263" aria-hidden="true">
      <path fill="var(--orange)" d="M0,88 C50,56 110,54 170,76 C240,102 300,148 372,154 C300,152 240,112 170,88 C110,68 50,74 0,101 Z"/>
      <path fill="var(--charcoal)" d="M0,107 C45,82 95,72 145,87 C220,112 290,168 366,160 C404,156 430,136 443,113 L443,263 L0,263 Z"/>
    </svg>
    <div class="brand-mark"></div>
    <div class="brand-name">Halloran Field Services</div>
    <ul class="service-list">
      <li>Bulk fertilizer including Lime<br>Gypsum, Manure &amp; Compost</li>
      <li>Granular fertilizer including<br>Single Super, Urea<br>Gran-am, &amp; Custom Blends</li>
      <li>Modern equipment</li>
      <li>Autosteer &amp; Variable Rate Capable</li>
      <li>Friendly &amp; Reliable Service</li>
    </ul>
    <div class="contact">
      <p class="contact-name">Contact GUS</p>
      <p class="contact-phone">0417 552 308</p>
    </div>
  </section>

  <section class="card card--brand">
    <div class="brand-mark--large"></div>
    <div class="brand-name--large">Halloran Field Services</div>
    <p class="tagline">CUSTOMISED SPREADING</p>
  </section>
</body>
</html>
```